Road Construction Company needs business cards

We would like a new business card designed for our business.

We're a road construction company based in Qld, Australia.

Can the business card please have the following information on it.

Name: Warren Halbeck
Position: General Manager
Phone: 0472 915 348
Email: Warren.halbeck@tovrin.com.au
Address: 87 Marrow Ave, Pendlebay, QLD, 4023
Website: www.tovrin.com.au

Visually we'd like the card to be professional and simple.

Attached is our logo.

Our website is www.tovrin.com.au

Target Market(s)

Men aged 25-60

Contact Information for Business Card

As listed in project description

Font styles to use
Serif

Requirements
Must have
• Large logo on back of card

```html
<!DOCTYPE html>
<html lang="en">
<head>
<meta charset="utf-8">
<title>Tovrin – Business Card</title>
<link rel="stylesheet" href="https://fonts.googleapis.com/css2?family=Open+Sans:wght@400;600;700;800&display=swap">
<style>
  :root {
    --backdrop: #2b2b30;
    --card: #1f1f24;
    --brand-blue: #1a5cb0;
    --accent-blue: #3ea6e0;
    --text-light: #f2f2f2;
    --divider: #8a8a92;
  }
  * { box-sizing: border-box; margin: 0; padding: 0; }
  html, body {
    width: 1200px; height: 780px; overflow: hidden;
    background: var(--backdrop);
    font-family: "Open Sans", Arial, sans-serif;
  }
  .sheet {
    width: 1200px; height: 780px;
    display: flex; align-items: center; justify-content: center; gap: 40px;
  }
  .card {
    position: relative;
    width: 550px; height: 314px;
    background: var(--card);
    box-shadow: 0 14px 30px rgba(0,0,0,.45);
    overflow: hidden;
  }
  .card__stripe {
    position: absolute; left: 0; top: 0; bottom: 0;
    width: 6px; background: var(--accent-blue);
  }
  .brand-name {
    color: var(--brand-blue);
    font-weight: 800;
    text-transform: uppercase;
    letter-spacing: 2px;
    line-height: 1;
  }
  .card--front .brand-name {
    position: absolute; left: 0; right: 0; top: 50%;
    transform: translateY(-50%);
    text-align: center; font-size: 92px;
  }
  .card--back .brand-name {
    position: absolute; left: 40px; top: 196px;
    font-size: 50px;
  }
  .card__divider {
    position: absolute; left: 282px; top: 40px; bottom: 40px;
    width: 1px; background: var(--divider);
  }
  .contact {
    position: absolute; left: 302px; top: 52px; right: 16px;
    color: var(--text-light);
  }
  .contact__name {
    color: var(--brand-blue); font-weight: 700; font-size: 25px; line-height: 1.1;
  }
  .contact__role { font-weight: 600; font-size: 14px; margin-top: 4px; }
  .contact__address { font-size: 13px; line-height: 1.45; margin-top: 16px; }
  .contact__list { list-style: none; margin-top: 16px; font-size: 13px; line-height: 1.5; }
  .contact__list li { display: flex; align-items: center; gap: 8px; white-space: nowrap; }
  .contact__icon { width: 13px; height: 13px; flex: none; fill: var(--accent-blue); }
</style>
</head>
<body>
<main class="sheet">
  <section class="card card--front">
    <div class="card__stripe"></div>
    <div class="brand-name">Tovrin</div>
  </section>

  <section class="card card--back">
    <div class="card__stripe"></div>
    <div class="brand-name">Tovrin</div>
    <div class="card__divider"></div>
    <div class="contact">
      <div class="contact__name">Warren Halbeck</div>
      <div class="contact__role">General Manager</div>
      <div class="contact__address">87 Marrow Ave,<br>Pendlebay, QLD, 4023</div>
      <ul class="contact__list">
        <li>
          <svg class="contact__icon" viewBox="0 0 24 24" aria-hidden="true"><path d="M6.6 10.8a15.1 15.1 0 0 0 6.6 6.6l2.2-2.2c.3-.3.7-.4 1-.2 1.1.4 2.3.6 3.6.6.6 0 1 .4 1 1V20c0 .6-.4 1-1 1A17 17 0 0 1 3 4c0-.6.4-1 1-1h3.5c.6 0 1 .4 1 1 0 1.3.2 2.5.6 3.6.1.3 0 .7-.2 1z"/></svg>
          0472 915 348
        </li>
        <li>
          <svg class="contact__icon" viewBox="0 0 24 24" aria-hidden="true"><path d="M12 2a10 10 0 1 0 0 20 10 10 0 0 0 0-20zm6.9 6h-2.9a15.7 15.7 0 0 0-1.4-3.6A8 8 0 0 1 18.9 8zM12 4c.8 1.2 1.5 2.5 1.9 4h-3.8c.4-1.5 1.1-2.8 1.9-4zM4.3 14a8 8 0 0 1 0-4h3.4a16 16 0 0 0 0 4zm.8 2h2.9c.3 1.3.8 2.5 1.4 3.6A8 8 0 0 1 5.1 16zM8 8H5.1a8 8 0 0 1 4.3-3.6C8.8 5.5 8.4 6.7 8 8zm4 12c-.8-1.2-1.5-2.5-1.9-4h3.8c-.4 1.5-1.1 2.8-1.9 4zm2.3-6H9.7a14.7 14.7 0 0 1 0-4h4.6a14.7 14.7 0 0 1 0 4zm.3 5.6c.6-1.1 1.1-2.3 1.4-3.6h2.9a8 8 0 0 1-4.3 3.6zm1.7-5.6a16 16 0 0 0 0-4h3.4a8 8 0 0 1 0 4z"/></svg>
          www.tovrin.com.au
        </li>
        <li>
          <svg class="contact__icon" viewBox="0 0 24 24" aria-hidden="true"><path d="M3 5h18c.6 0 1 .4 1 1v12c0 .6-.4 1-1 1H3c-.6 0-1-.4-1-1V6c0-.6.4-1 1-1zm9 7.2L4.5 7v10h15V7z"/></svg>
          Warren.halbeck@tovrin.com.au
        </li>
      </ul>
    </div>
  </section>
</main>
</body>
</html>
```